TalkHarbor - Language Coaching Services

Sleek, innovative, trendy design for Language Coaching business.

TalkHarbor is a new UK based company that provides Language Coaching services. We offer highly personalized on-line and face to face language courses. We also impart learning techniques workshops based on the latest neuroscience research for second-language acquisition.

Target Market(s)

See attached info

Industry/Entity Type

Consulting

Contact Information for Business Card

TalkHarbor
DaniaKV@talkharbor.co.uk
TalkHarbor.co.uk
London, UK

Font styles to use
Sans Serif

```html
<!DOCTYPE html>
<html lang="en">
<head>
<meta charset="utf-8">
<title>TalkHarbor Business Card</title>
<link href="https://fonts.googleapis.com/css2?family=Montserrat:wght@400;500&family=Lato:wght@400;700&display=swap" rel="stylesheet">
<style>
  :root {
    --backdrop: #2a2b2e;
    --card-dark: #111821;
    --card-dark-edge: #1a2430;
    --logo-blue: #5a8fd6;
    --teal: #1f8db3;
    --teal-deep: #177ea3;
    --paper: #fbfbfb;
    --white: #ffffff;
  }
  * { margin: 0; padding: 0; box-sizing: border-box; }
  html, body {
    width: 1200px; height: 900px; overflow: hidden;
    background: var(--backdrop);
  }
  .canvas {
    position: relative; width: 1200px; height: 900px;
  }
  .card {
    position: absolute; left: 320px; width: 560px; height: 320px;
    overflow: hidden; box-shadow: 0 14px 30px rgba(0,0,0,.45);
  }
  .card--front { top: 90px; background: radial-gradient(ellipse at 50% 45%, var(--card-dark-edge), var(--card-dark) 75%); }
  .card--back { top: 490px; background: var(--paper); }

  .brand {
    position: absolute; left: 0; right: 0;
    display: flex; flex-direction: column; align-items: center;
  }
  .brand__circle {
    width: 78px; height: 78px; border-radius: 50%;
    border: 6px solid currentColor; margin-bottom: 12px;
  }
  .brand__name {
    font-family: "Montserrat", sans-serif; font-weight: 500;
    font-size: 44px; letter-spacing: 1px; line-height: 1;
  }
  .card--front .brand { top: 70px; color: var(--logo-blue); }
  .card--back .brand { top: 26px; color: var(--teal); }
  .card--back .brand__circle { width: 62px; height: 62px; border-width: 5px; margin-bottom: 8px; }
  .card--back .brand__name { font-size: 36px; }

  .website {
    position: absolute; top: 246px; left: 0; right: 0; text-align: center;
    font-family: "Montserrat", sans-serif; font-size: 14px;
    letter-spacing: 5px; color: var(--white);
  }

  .band {
    position: absolute; left: 0; right: 0; bottom: 0; height: 132px;
    background: var(--teal);
  }
  .band__rule {
    position: absolute; left: 0; right: 0; height: 2px; background: var(--teal);
  }
  .band__rule--outer { bottom: 140px; }
  .band__rule--inner { bottom: 136px; }

  .holder {
    position: absolute; left: 60px; bottom: 44px; color: var(--white);
    font-family: "Lato", sans-serif;
  }
  .holder__name { font-size: 18px; font-weight: 400; }
  .holder__name b { font-weight: 700; }
  .holder__role { font-size: 12px; margin-top: 3px; }

  .divider {
    position: absolute; left: 290px; bottom: 24px; width: 2px; height: 84px;
    background: var(--white);
  }
  .contact {
    position: absolute; left: 318px; bottom: 30px; list-style: none;
    font-family: "Lato", sans-serif; font-size: 13px; color: var(--white);
  }
  .contact__item { display: flex; align-items: center; gap: 10px; height: 24px; }
  .contact__icon { width: 16px; height: 16px; flex: none; }
</style>
</head>
<body>
<main class="canvas">

  <section class="card card--front" aria-label="Business card front">
    <div class="brand">
      <span class="brand__circle"></span>
      <span class="brand__name">TalkHarbor</span>
    </div>
    <p class="website">www.TalkHarbor.co.uk</p>
  </section>

  <section class="card card--back" aria-label="Business card back">
    <div class="brand">
      <span class="brand__circle"></span>
      <span class="brand__name">TalkHarbor</span>
    </div>
    <span class="band__rule band__rule--outer"></span>
    <span class="band__rule band__rule--inner"></span>
    <div class="band">
      <div class="holder">
        <p class="holder__name">Maren <b>Holloway</b></p>
        <p class="holder__role">Chief Executive Offer</p>
      </div>
      <span class="divider"></span>
      <ul class="contact">
        <li class="contact__item">
          <svg class="contact__icon" viewBox="0 0 16 16"><circle cx="8" cy="8" r="8" fill="#fff"/><path d="M4 6.5c0-1 1.5-1.8 4-1.8s4 .8 4 1.8v.8H10v-.8H6v.8H4z M5 8h6l.8 3.5H4.2z" fill="#1f8db3"/></svg>
          <span>020.7946.0381</span>
        </li>
        <li class="contact__item">
          <svg class="contact__icon" viewBox="0 0 16 16"><circle cx="8" cy="8" r="8" fill="#fff"/><rect x="4" y="6" width="8" height="5" rx="1" fill="#1f8db3"/><rect x="5.5" y="4" width="5" height="2.5" fill="#1f8db3"/></svg>
          <span>020.7946.0527</span>
        </li>
        <li class="contact__item">
          <svg class="contact__icon" viewBox="0 0 16 16"><circle cx="8" cy="8" r="8" fill="#fff"/><rect x="4" y="5" width="8" height="6" fill="#1f8db3"/><path d="M4 5l4 3.5L12 5" stroke="#fff" stroke-width="1" fill="none"/></svg>
          <span>DaniaKV@talkharbor.co.uk</span>
        </li>
      </ul>
    </div>
  </section>

</main>
</body>
</html>
```